Sophisticated, clean website reflecting my feminine, playful side to sell my abstract art,

I need a website no more than 3 pages to showcase my paintings, a little about me and some contact info. I do abstracts so looking for something a little edgy, yet feminine and current.
Updates

Hi there, These are some artists websites that I Iike: Marnelvoss.com (I like how airy it is) peterwallombry.com garethpolvens.com (I like how it scrolls) I'll need a place for a photo ( a headshot-i do not have it yet so I'll need to be able to upload that later) as well as an area for my bio. Also, it's important that I will be able to upload any new photos and descriptions easily so it should be user friendly. Lastly, I like in a sunny place so would like to have this seem upbeat and playful as that is how i like to paint. thanks-I'm trying to upload my photos now -

Target Market(s)

ppl ages 35-70 who want large scale art for their homes

Industry/Entity Type

art

Coding

Coded - Design and coding required

Number of Pages Required

3 page

Colors

Designer to choose colors to be used in the design.

Requirements
Must have
• photos of my art, a place for my bio, be easy to reach me. tasteful-nothing too "in your face" -my clients are pretty high end and organized. They like clean lines
Nice to have
• sophisticated background, muted tones in the back-similar clean font throughout-no cursive
Should not have
• too many dark areas. Too many blocks of color. Too serious.

```html
<!DOCTYPE html>
<html lang="en">
<head>
<meta charset="utf-8">
<title>Lena Marchetti Art</title>
<link href="https://fonts.googleapis.com/css2?family=Roboto:wght@400;500;700&family=Great+Vibes&display=swap" rel="stylesheet">
<style>
:root{
  --magenta:#b50f8c;
  --ink:#222;
  --muted:#555;
  --white:#fff;
  --paper:#f3f1f2;
  --black:#000;
  --dots:#b50f8c;
}
*{box-sizing:border-box;margin:0;padding:0}
html,body{width:1200px;height:2586px;overflow:hidden}
body{position:relative;font-family:'Roboto',sans-serif;color:var(--ink);background:var(--white)}
.abs{position:absolute}
.topline{left:0;top:0;width:1200px;height:5px;background:var(--magenta)}
.header{left:0;top:5px;width:1200px;height:80px;background:var(--white)}
.brand{font-family:'Roboto',sans-serif;font-weight:500;color:#111;font-size:27px;left:96px;top:30px}
.nav{left:397px;top:38px;display:flex;gap:35px;font-size:15px;color:#333}
.nav .active{color:var(--magenta);border-bottom:2px solid var(--magenta);padding-bottom:3px}
.phone-ico{left:704px;top:26px;width:43px;height:43px;border-radius:50%;background:var(--magenta)}
.phone-num{left:757px;top:38px;font-size:17px;font-weight:700;color:#111}
.cart{left:921px;top:40px}
.cart-badge{left:940px;top:32px;width:18px;height:18px;border-radius:50%;background:var(--magenta);color:#fff;font-size:11px;text-align:center;line-height:18px;font-weight:700}
.btn{display:inline-flex;align-items:center;gap:14px;background:var(--magenta);color:#fff;font-weight:700;font-size:15px;text-transform:uppercase}
.login{left:987px;top:23px;width:116px;height:49px;justify-content:center}
.hero{left:0;top:85px;width:1200px;height:805px;background:linear-gradient(100deg,#5a3a2a 0%,#3d2a3a 30%,#2a2045 55%,#1d2350 75%,#2b1f3a 100%)}
.hero-art{left:0;top:85px;width:600px;height:700px;background:radial-gradient(ellipse at 45% 55%,#c9b9b4 0%,#8a6a55 35%,rgba(60,40,40,0) 70%)}
.hero-title{left:566px;top:358px;width:534px;text-align:right;color:#fff;font-size:58px;font-weight:500}
.hero-text{left:578px;top:455px;width:500px;text-align:center;color:#fff;font-size:16px;line-height:28px}
.hero-btn{left:744px;top:544px;width:177px;height:53px;justify-content:center}
.script{font-family:'Great Vibes',cursive;color:#111}
.dots{height:6px;background:radial-gradient(circle,var(--dots) 2.5px,transparent 3px) 0 0/10px 6px}
.sec-title{left:0;width:1200px;top:918px;text-align:center;font-size:58px}
.frame{top:1038px;width:310px;height:330px;border:7px solid #111;box-shadow:0 3px 8px rgba(0,0,0,.4)}
.f1{left:110px;background:linear-gradient(135deg,#e9e3d6,#d7a53a 30%,#2d4c8c 55%,#efe9e2 80%)}
.f2{left:445px;background:linear-gradient(135deg,#c04fb0,#9c2b8e 50%,#c25bb8)}
.f3{left:780px;background:linear-gradient(135deg,#ddd8d8,#7a3a2a 35%,#e5dcd9 60%,#5a2a1e 85%)}
.cart-circle{left:576px;top:1180px;width:48px;height:48px;border-radius:50%;background:#fff}
.about{left:0;top:1450px;width:1200px;height:720px;background:var(--paper)}
.portrait{left:107px;top:1530px;width:444px;height:444px;border-radius:50%;border:9px solid var(--magenta);background:linear-gradient(150deg,#e8e2d8,#d9b89a 40%,#b97b5e 70%,#e0ccb5)}
.about-title{left:608px;top:1530px;font-size:56px}
.about-text{left:622px;top:1622px;width:472px;font-size:16.3px;line-height:25.6px;color:var(--muted);text-align:justify}
.about-btn{left:622px;top:1903px;width:177px;height:53px;justify-content:center}
.footer{left:0;top:2150px;width:1200px;height:436px;background:var(--black);color:#fff}
.f-head{font-size:17px;font-weight:700;text-decoration:underline;color:#fff}
.f-text{font-size:16px;color:#eee;line-height:26px}
.email-box{left:109px;top:2345px;width:275px;height:49px;background:#1b1b1b;font-size:13px;color:#ddd;display:flex;align-items:center;gap:16px;padding-left:16px}
.sub-btn{left:109px;top:2411px;width:151px;height:50px;justify-content:center;font-size:14px}
.c-ico{width:43px;height:43px;border-radius:50%;background:#1e1e1e;display:flex;align-items:center;justify-content:center}
.c-row{left:482px;display:flex;align-items:center;gap:18px;font-size:16px;color:#fff}
.social{left:840px;top:2421px;display:flex;gap:10px}
.social span{width:39px;height:39px;border-radius:50%;border:1px solid #fff}
.divider{left:109px;top:2511px;width:981px;height:1px;background:#555}
.copy{left:0;width:1200px;top:2541px;text-align:center;font-size:13px;color:#fff}
</style>
</head>
<body>
<div class="abs topline"></div>
<header class="abs header"></header>
<div class="abs brand">Lena Marchetti Art</div>
<nav class="abs nav"><span class="active">HOME</span><span>ABOUT ME</span><span>CONTACT US</span></nav>
<div class="abs phone-ico"><svg width="43" height="43" viewBox="0 0 43 43"><path d="M15 13c1-1 2-1 3 0l2 3c.6 1 .3 1.8-.4 2.4l-1 .8c1 2 3 4 5 5l.8-1c.6-.7 1.4-1 2.4-.4l3 2c1 1 1 2 0 3-2 2-4 2-7 0s-7-6-8.5-9C13.5 17 13 15 15 13z" fill="#fff"/></svg></div>
<div class="abs phone-num">+1 888 888 8888</div>
<svg class="abs cart" width="24" height="22" viewBox="0 0 24 22"><path d="M0 2h4l3 11h12l3-8H6" fill="none" stroke="#111" stroke-width="2.5"/><path d="M6 5h16l-3 8H8z" fill="#111"/><circle cx="9" cy="18" r="2" fill="#111"/><circle cx="18" cy="18" r="2" fill="#111"/></svg>
<div class="abs cart-badge">0</div>
<div class="abs btn login">LOGIN <svg width="11" height="13" viewBox="0 0 11 13"><rect x="0" y="5" width="11" height="8" fill="#fff"/><path d="M2.5 5V3.5a3 3 0 016 0V5" fill="none" stroke="#fff" stroke-width="1.8"/></svg></div>

<div class="abs hero" role="img" aria-label="Studio photo: colourful paint backdrop, easel with floral abstract canvas and brushes"></div>
<div class="abs hero-art"></div>
<h1 class="abs hero-title">Lena Marchetti Art</h1>
<p class="abs hero-text">Lorem ipsum dolor sit amet, consectetur adipiscing elit, sed do eiusmod tempor incididunt ut labore et dolore magna aliqua enim ad minimd.</p>
<div class="abs btn hero-btn">GET STARTED <svg width="17" height="17" viewBox="0 0 17 17"><circle cx="8.5" cy="8.5" r="8.5" fill="#fff"/><path d="M7 5l4 3.5L7 12" fill="none" stroke="#b50f8c" stroke-width="2.2"/></svg></div>

<svg class="abs" style="left:0;top:730px" width="1200" height="165" viewBox="0 0 1200 165">
  <path d="M0 100C150 30 300 5 430 18C620 38 760 130 950 142C1080 150 1150 135 1200 112V165H0Z" fill="var(--magenta)"/>
  <path d="M0 130C150 55 300 25 430 38C620 58 740 140 930 158C1080 168 1150 158 1200 150V165H0Z" fill="#fff"/>
</svg>

<h2 class="abs script sec-title">My Paintings</h2>
<div class="abs dots" style="left:560px;top:983px;width:80px"></div>
<div class="abs frame f1" role="img" aria-label="Abstract painting with blue and gold swirls"></div>
<div class="abs frame f2" role="img" aria-label="Abstract floral painting with magenta overlay"></div>
<div class="abs frame f3" role="img" aria-label="Abstract painting of brown and pink roses"></div>
<div class="abs cart-circle"><svg width="48" height="48" viewBox="0 0 48 48"><path d="M17 18h3l2 8h8l2-6H21" fill="var(--magenta)" stroke="var(--magenta)" stroke-width="1.5"/><circle cx="23" cy="30" r="1.3" fill="var(--magenta)"/><circle cx="29" cy="30" r="1.3" fill="var(--magenta)"/></svg></div>

<section class="abs about"></section>
<div class="abs portrait" role="img" aria-label="Photo of the artist painting at an easel holding a palette"></div>
<h2 class="abs script about-title">About Us</h2>
<div class="abs dots" style="left:622px;top:1597px;width:80px"></div>
<p class="abs about-text">Lorem ipsum dolor sit amet, consectetur adipiscing elit, sed do eius­mod tempor incididunt ut labore et dolore magna aliqua. Ut enim ad minim veniam, quis nostrud exercitation ullamco laboris nisi ut aliquip ex ea commodo consequat. Duis aute irure dolor in reprehenderit in voluptate velit esse cillum dolore eu fugiat nulla pariatur. Excepteur sint occaecat cupidatat non proident, sunt culpa qui officia deserunt mollit anim id est laborum.Lorem ipsum dolor sit amet, consectetur adipiscing elit, sed do eiusmod tempor incididunt ut labore et dolore magna aliqua. Ut enim ad minim veniam, quis nostrud exercitation ullamco laboris nisi ut aliquip ex ea commodo consequat.</p>
<div class="abs btn about-btn">GET STARTED <svg width="17" height="17" viewBox="0 0 17 17"><circle cx="8.5" cy="8.5" r="8.5" fill="#fff"/><path d="M7 5l4 3.5L7 12" fill="none" stroke="#b50f8c" stroke-width="2.2"/></svg></div>

<footer class="abs footer"></footer>
<svg class="abs" style="left:0;top:2020px" width="1200" height="160" viewBox="0 0 1200 160">
  <path d="M0 25C200 -10 420 30 640 80C800 118 900 140 1000 128C1100 115 1160 70 1200 40V160H0Z" fill="var(--magenta)"/>
  <path d="M0 60C200 20 420 50 640 100C800 135 900 152 1000 140C1100 126 1160 85 1200 65V160H0Z" fill="var(--black)"/>
</svg>

<div class="abs f-head" style="left:109px;top:2255px">NEWSLETTER</div>
<div class="abs f-text" style="left:109px;top:2300px">Enter your email &amp; subcribing newsletter</div>
<div class="abs email-box"><svg width="13" height="10" viewBox="0 0 13 10"><rect x=".5" y=".5" width="12" height="9" fill="none" stroke="#b50f8c"/><path d="M.5 .5l6 5 6-5" fill="none" stroke="#b50f8c"/></svg>Email address</div>
<div class="abs btn sub-btn">SUBSCRIBE <svg width="16" height="16" viewBox="0 0 16 16"><circle cx="8" cy="8" r="8" fill="#fff"/><path d="M4 8l8-3-3 8-1-4z" fill="var(--magenta)"/></svg></div>

<div class="abs f-head" style="left:482px;top:2255px">CONTACT&nbsp; INFORMATION</div>
<div class="abs c-row" style="top:2301px"><span class="c-ico"><svg width="18" height="14" viewBox="0 0 18 14"><rect x="1" y="1" width="16" height="12" rx="2" fill="none" stroke="#fff" stroke-width="1.6"/><path d="M1 2l8 6 8-6" fill="none" stroke="#fff" stroke-width="1.6"/></svg></span>info@lenamarchettiart.com</div>
<div class="abs c-row" style="top:2371px;font-weight:700;font-size:17px"><span class="c-ico"><svg width="16" height="16" viewBox="0 0 16 16"><path d="M3 1c1-1 2-1 2.5 0l1.5 2.5c.5.8.2 1.5-.4 2l-.8.6c.8 1.6 2.4 3.2 4 4l.6-.8c.5-.6 1.2-.9 2-.4L15 10.5c1 .5 1 1.5 0 2.5-1.6 1.6-3.5 1.6-6 0S3.5 8.5 2 6C.8 4 1.4 2.6 3 1z" fill="#fff"/></svg></span>+1 888 888 8888</div>
<div class="abs c-row" style="top:2441px"><span class="c-ico"><svg width="14" height="18" viewBox="0 0 14 18"><path d="M7 0a7 7 0 017 7c0 5-7 11-7 11S0 12 0 7a7 7 0 017-7z" fill="#fff"/><circle cx="7" cy="7" r="2.5" fill="#1e1e1e"/></svg></span>345,Lorem ipsum dolored</div>

<div class="abs" style="left:840px;top:2252px;font-size:26px;font-weight:500;color:#fff">Lena Marchetti Art</div>
<div class="abs f-text" style="left:840px;top:2306px;width:250px">Lorem ipsum dolor sit&nbsp; consectetur adipiscing&nbsp; sed do eiusmod tempor</div>
<div class="abs f-head" style="left:840px;top:2378px">FOLLOW US</div>
<div class="abs social"><span></span><span></span><span></span><span></span></div>

<div class="abs divider"></div>
<div class="abs copy">2022 ©&nbsp; Copyrights Lena Marchetti Art&nbsp; All rights reserved.</div>
</body>
</html>
```